Modern Minimalist photo holiday card

I need a few designs for a photo holiday card that is modern , minimalist yet chic. Some examples on the web of things that I like -

http://www.velmocards.example/product/47065/flat_holiday_photo_cards_dapper_tilde.html
http://www.velmocards.example/product/48654/flat_holiday_photo_cards_sunny_lantern.html

http://www.kervalab.example/studio-brindle-minimalist-holiday-card-collection/

Target Market(s)

Customers would be American educated professional living in big cities and suburbs. They will most likely be females from 20 to 50.

Industry/Entity Type

Product

Requirements
Must have
• The cards are 5 by 7 folded. I need the design to support 1 photo preferably taking up the whole space with stylized words. No traditional holiday bells etc. Just a hint of holiday is fine. Need 4 designs to begin with. Please quote for 4 distinct designs as a package. You can use any photo you want.

The users submit their photos so the designs should work with many different photos and should not depend on the content of the photo. Users will be able to change the location of text so text placement can depend on the photo. If the colors are coordinated with the photo please provide some alternate colors ( for user to choose)

```html
<!DOCTYPE html>
<html lang="en">
<head>
<meta charset="utf-8">
<title>Merry Christmas Card</title>
<link rel="stylesheet" href="https://fonts.googleapis.com/css2?family=Poiret+One&display=swap">
<style>
  :root {
    --paper: #f3f3f3;
    --gold: #ffe01b;
    --gold-soft: #ffe95e;
  }
  html, body {
    margin: 0;
    padding: 0;
    width: 857px;
    height: 1200px;
    overflow: hidden;
    background: var(--paper);
  }
  .card {
    position: relative;
    width: 857px;
    height: 1200px;
    background: var(--paper);
    overflow: hidden;
  }
  .greeting {
    position: absolute;
    top: 14px;
    right: 24px;
    margin: 0;
    font-family: "Poiret One", cursive;
    font-weight: 400;
    font-size: 86px;
    line-height: 1.4;
    color: var(--gold);
    white-space: nowrap;
    letter-spacing: 1px;
  }
  .snowflake-cluster {
    position: absolute;
    left: 0;
    top: 700px;
    width: 560px;
    height: 500px;
  }
</style>
</head>
<body>
  <main class="card">
    <h1 class="greeting">Merry Christmas</h1>

    <svg class="snowflake-cluster" viewBox="0 700 560 500" role="img"
         aria-label="Cluster of yellow paper-cut snowflakes of different sizes in the lower left corner">
      <defs>
        <radialGradient id="flake-glow">
          <stop offset="0%" stop-color="var(--gold)" stop-opacity="0.95"/>
          <stop offset="70%" stop-color="var(--gold-soft)" stop-opacity="0.6"/>
          <stop offset="100%" stop-color="var(--gold-soft)" stop-opacity="0"/>
        </radialGradient>
      </defs>
      <g fill="url(#flake-glow)">
        <circle cx="83" cy="845" r="131"/>
        <circle cx="262" cy="928" r="48"/>
        <circle cx="179" cy="1028" r="79"/>
        <circle cx="317" cy="1023" r="29"/>
        <circle cx="67" cy="1126" r="38"/>
        <circle cx="209" cy="1152" r="38"/>
        <circle cx="424" cy="1131" r="131"/>
      </g>
    </svg>
  </main>
</body>
</html>
```